Employment Agency Website Design

We are working with an employment agency in California.

Some sites to use for content/competitors and inspiration:

https://www.pinecrestjobs.com/us/en
https://www.velmorusa.com
https://www.dravenworks.us
https://www.quillora.com/en
https://www.tomvalusa.com
https://www.fernstaffing.com

Thank you for taking the time to consider designing a website for us. We are web developers based in Stockton, CA, USA. Most of our projects go through the same process. Understanding this process may help you win a project with us. We custom-code all of our websites in-house. We don’t have any requirements as to what tools you use for your design, but we prefer Figma files. For any design that we label as four-stars, we send it to the client for review. The client picks the final design they want us to use. Once we complete this process, we will continue to show additional clients all the four-star sites and purchase them later. Your designs will have multiple chances to sell. For better chances of success, we ask that you follow these guidelines.

IMAGES:
If you use any images or icons in the design, we ask that you have a link to the asset so we can purchase the image/icon. Most of the designs we submit do not have the customer’s images on them unless they have some great images. Be creative; show us the feeling you are trying to portray with your image choices. Use any royalty-free site you choose. We subscribe to Adobe and mainly use their images, but we can purchase images outside of Adobe. PLEASE NOTE: we will not submit designs to clients with watermarks on the images.

FONTS:
We ask that you identify the fonts used in the design. This can be done in a message if you want. We typically use Google Fonts and Adobe Fonts.

CONTENT:
We're always open to different content and ideas. We often submit designs with stock images so the client can see our vision. We typically take pictures after the website launch to use their images with our vision. Lorem Ipsum is fine for paragraphs, but we ask that you write the headers in correct English. We want to be able to show the vision and identify the sections of the website.

INSPIRATION:
We typically add a couple of links in the brief of websites we like to help you get started in your design.

REVISIONS:
We do not often ask for revisions of the designs unless we see something in the design that may not appeal to the client. If there are slight changes that we want to make, we do that in the development process.

FEEDBACK:
We rarely give feedback on designs during the design process. We are working on many website projects and do not have the time to provide feedback. We usually respond if your request is well thought out and asks specific questions, but a note asking “feedback, please” usually goes unanswered.

```html
<!DOCTYPE html>
<html lang="en">
<head>
<meta charset="utf-8">
<title>kestrelwork — Find your job</title>
<link href="https://fonts.googleapis.com/css2?family=Poppins:wght@400;500;600;700&display=swap" rel="stylesheet">
<style>
:root{
  --brand:#c8202f;
  --brand-dark:#b01a28;
  --ink:#2b2b2b;
  --muted:#8a8a8a;
  --soft:#efefef;
  --tile:#ececec;
  --white:#ffffff;
}
*{box-sizing:border-box;margin:0;padding:0}
html,body{width:1200px;height:4471px;overflow:hidden;background:var(--white)}
body{position:relative;font-family:'Poppins',sans-serif;color:var(--ink)}
.abs{position:absolute}

/* nav */
.site-nav{position:absolute;left:0;top:0;width:1200px;height:83px;background:var(--white)}
.brand{position:absolute;display:flex;align-items:center;gap:8px}
.brand-mark{width:26px;height:26px;border-radius:50%;background:var(--brand)}
.brand-name{font-weight:600;font-size:25px;color:var(--brand);letter-spacing:-.5px;line-height:1}
.brand-tag{font-size:8px;color:var(--muted)}
.nav-links{position:absolute;left:297px;top:29px;display:flex;gap:30px;font-size:18px}
.nav-links a{color:var(--ink);text-decoration:none}
.nav-links a.active{text-decoration:underline}
.login{position:absolute;left:983px;top:17px;width:132px;height:49px;border-radius:25px;background:var(--brand);color:#fff;font-weight:600;font-size:19px;display:flex;align-items:center;justify-content:center}

/* hero */
.hero{position:absolute;left:0;top:83px;width:1200px;height:612px;background:var(--brand)}
.hero-photo{position:absolute;left:663px;top:0;width:537px;height:612px;background:linear-gradient(150deg,#a86b52 0%,#c79a80 40%,#e8ddd2 70%,#8b8f97 100%)}
.hero h1{position:absolute;left:83px;top:140px;width:520px;font-size:34px;font-weight:600;line-height:47px;color:#fff}
.hero p{position:absolute;left:83px;top:254px;width:455px;font-size:19px;line-height:30px;color:#fff}
.pill{position:absolute;top:365px;height:50px;border-radius:25px;font-weight:600;font-size:18px;display:flex;align-items:center;justify-content:center;color:#fff}
.pill.outline{left:83px;width:152px;border:2px solid #fff}
.pill.solid{left:269px;width:177px;background:#fff;color:var(--brand)}

.page-soft{position:absolute;left:0;top:695px;width:1200px;height:981px;background:var(--soft)}

/* search */
.search-bar{position:absolute;left:83px;top:657px;width:1032px;height:93px;background:#fff;border-radius:6px;box-shadow:0 6px 16px rgba(0,0,0,.12)}
.field{position:absolute;top:17px;width:238px;height:57px;background:var(--soft);border-radius:6px;display:flex;align-items:center;gap:16px;padding-left:20px;font-size:19px;color:#4a4a4a}
.search-btn{position:absolute;left:862px;top:23px;width:137px;height:50px;border-radius:25px;background:var(--brand);color:#fff;font-weight:600;font-size:18px;display:flex;align-items:center;justify-content:center}

.section-title{position:absolute;left:0;width:1200px;text-align:center;font-weight:600;font-size:27px}
.section-sub{position:absolute;left:0;width:1200px;text-align:center;font-size:19px;line-height:30px;color:var(--muted)}

/* categories */
.cat{position:absolute;width:310px;height:283px;background:#fff;border-radius:12px;box-shadow:0 6px 14px rgba(0,0,0,.1);text-align:center}
.cat .icon{position:absolute;left:113px;top:31px;width:84px;height:84px;border-radius:50%;background:var(--brand);display:flex;align-items:center;justify-content:center}
.cat h3{position:absolute;top:138px;width:100%;font-size:20px;font-weight:600}
.cat p{position:absolute;top:182px;left:0;width:100%;font-size:18px;line-height:28px;color:var(--muted)}
.cat.featured{background:var(--brand);color:#fff}
.cat.featured .icon{background:#fff}
.cat.featured p{color:#fff}

/* steps */
.step-circle{position:absolute;width:166px;height:166px;border-radius:50%;background:var(--brand);display:flex;align-items:center;justify-content:center}
.step-text{position:absolute;text-align:center;font-size:19px;line-height:30px;color:var(--muted)}

/* about */
.about-photo{position:absolute;left:83px;top:2406px;width:418px;height:370px;border-radius:14px;background:linear-gradient(135deg,#e4e6ea 0%,#c9ccd2 50%,#f2f2f2 100%)}
.about h2{position:absolute;left:551px;top:2406px;font-size:27px;font-weight:600}
.about p{position:absolute;left:551px;top:2455px;width:475px;font-size:19px;line-height:30px;color:var(--muted)}
.stat{position:absolute;top:2616px;height:142px;border-radius:8px;background:var(--tile);text-align:center}
.stat b{display:block;margin-top:20px;font-size:27px;font-weight:600}
.stat span{display:block;margin-top:6px;font-size:19px;line-height:30px;color:var(--muted)}

/* popular */
.popular{position:absolute;left:0;top:2809px;width:1200px;height:606px;background:var(--brand)}
.job{position:absolute;top:215px;width:483px;height:334px;background:#fff;border-radius:10px}
.job .company{position:absolute;left:25px;top:30px;display:flex;align-items:center;gap:14px;font-size:21px;font-weight:600}
.job .company i{display:block;width:40px;height:40px;border-radius:6px;background:var(--ink)}
.job .salary{position:absolute;right:25px;top:38px;font-size:21px;font-weight:600}
.job .salary small{font-size:19px;font-weight:400;color:var(--muted)}
.job h4{position:absolute;left:25px;top:108px;font-size:21px;font-weight:600}
.job .type{position:absolute;left:25px;top:145px;font-size:19px;color:var(--muted)}
.job .desc{position:absolute;left:25px;top:190px;width:360px;font-size:17px;line-height:28px;color:var(--muted)}
.job .apply{position:absolute;left:46px;top:269px;width:392px;height:49px;border-radius:25px;background:var(--brand);color:#fff;font-weight:600;font-size:18px;display:flex;align-items:center;justify-content:center}

/* stories */
.story{position:absolute;top:3655px;width:318px;height:316px;background:var(--brand);border-radius:6px 6px 40px 6px;color:#fff;text-align:center}
.story .avatar{position:absolute;left:117px;top:29px;width:84px;height:84px;border-radius:50%;background:linear-gradient(160deg,#f1ece6,#c7b7a6)}
.story h4{position:absolute;top:133px;width:100%;font-size:23px;font-weight:600}
.story p{position:absolute;top:185px;left:49px;width:220px;font-size:19px;line-height:30px}
.dot{position:absolute;top:4000px;width:24px;height:24px;border-radius:50%;background:var(--brand)}
.dot.idle{opacity:.45}

/* footer */
.site-footer{position:absolute;left:0;top:4054px;width:1200px;height:417px;background:var(--brand);color:#fff}
.social{position:absolute;top:4240px;width:38px;height:38px;border-radius:50%;background:#fff}
.foot-col{position:absolute;top:4115px}
.foot-col h5{font-size:21px;font-weight:600;margin-bottom:14px}
.foot-col a{display:block;color:#fff;text-decoration:none;font-size:18px;line-height:39px;font-weight:500}
.foot-rule{position:absolute;left:83px;top:4405px;width:1032px;height:1px;background:rgba(255,255,255,.7)}
.foot-legal{position:absolute;left:0;top:4421px;width:1200px;text-align:center;font-size:19px;font-weight:500;color:#fff}
</style>
</head>
<body>

<header class="site-nav">
  <div class="brand" style="left:87px;top:22px">
    <span class="brand-mark"></span><span class="brand-name">kestrelwork</span>
  </div>
  <div class="brand-tag abs" style="left:121px;top:50px">Careers made simple</div>
  <nav class="nav-links">
    <a class="active" href="#">Find Job</a><a href="#">Hire Telent</a><a href="#">Explore Consulting Solution</a><a href="#">Discover Insight</a>
  </nav>
  <div class="login">Login</div>
</header>

<section class="hero">
  <div class="hero-photo" role="img" aria-label="Photo of two women talking across a desk with a tablet in an office"></div>
  <h1>Anything’s possible when you have the talent</h1>
  <p>We provide job vacancies that you can visit if you are looking for work</p>
  <div class="pill outline">Find your job</div>
  <div class="pill solid">Find your telent</div>
</section>

<div class="page-soft"></div>

<div class="search-bar">
  <div class="field" style="left:33px">
    <svg width="24" height="24" viewBox="0 0 24 24" fill="none" stroke="#333" stroke-width="2.5"><circle cx="10" cy="10" r="7"/><path d="M15 15l6 6"/></svg>Search
  </div>
  <div class="field" style="left:304px">
    <svg width="24" height="24" viewBox="0 0 24 24"><path d="M12 2a7 7 0 0 0-7 7c0 5 7 13 7 13s7-8 7-13a7 7 0 0 0-7-7z" fill="#333"/><circle cx="12" cy="9" r="2.6" fill="#eee"/></svg>New York City
  </div>
  <div class="field" style="left:575px">
    <svg width="24" height="24" viewBox="0 0 24 24" fill="none" stroke="#333" stroke-width="2"><rect x="3" y="4" width="18" height="13" rx="1"/><path d="M7 20h10M7 9h5M7 12h8"/></svg>Job Level
  </div>
  <div class="search-btn">Search Job</div>
</div>

<h2 class="section-title" style="top:818px">Job categories that you can choose</h2>
<p class="section-sub" style="top:878px">We provide several job categories that are very<br>suitable for you</p>

<div class="cat" style="left:83px;top:1016px">
  <div class="icon"><svg width="40" height="40" viewBox="0 0 40 40" fill="none" stroke="#fff" stroke-width="2.5"><rect x="6" y="8" width="28" height="20" rx="2"/><path d="M14 34h12M20 28v6M11 14h10M11 19h18"/></svg></div>
  <h3>Design and Creative</h3><p>372 vacancies<br>available</p>
</div>
<div class="cat featured" style="left:445px;top:1016px">
  <div class="icon"><svg width="40" height="40" viewBox="0 0 40 40"><rect x="8" y="10" width="24" height="24" rx="3" fill="#c8202f"/><rect x="16" y="6" width="8" height="7" rx="1" fill="#c8202f"/><circle cx="20" cy="20" r="3.5" fill="#fff"/><path d="M13 30c1-4 13-4 14 0z" fill="#fff"/></svg></div>
  <h3>Admin</h3><p>124 vacancies<br>available</p>
</div>
<div class="cat" style="left:806px;top:1016px">
  <div class="icon"><svg width="40" height="40" viewBox="0 0 40 40" fill="none" stroke="#fff" stroke-width="2.5"><rect x="6" y="8" width="28" height="20" rx="2"/><path d="M14 34h12M17 14l-3 4 3 4M23 14l3 4-3 4"/></svg></div>
  <h3>Industrial IT</h3><p>68 vacancies<br>available</p>
</div>
<div class="cat" style="left:83px;top:1343px">
  <div class="icon"><svg width="40" height="40" viewBox="0 0 40 40" fill="none" stroke="#fff" stroke-width="2.5"><circle cx="20" cy="16" r="7"/><path d="M10 17a10 10 0 0 1 20 0M8 34c2-7 22-7 24 0"/></svg></div>
  <h3>Service</h3><p>372 vacancies<br>available</p>
</div>
<div class="cat" style="left:445px;top:1343px">
  <div class="icon"><svg width="40" height="40" viewBox="0 0 40 40"><circle cx="13" cy="15" r="6" fill="#fff"/><circle cx="20" cy="11" r="7" fill="#fff"/><circle cx="27" cy="15" r="6" fill="#fff"/><rect x="12" y="17" width="16" height="15" rx="2" fill="#fff"/></svg></div>
  <h3>Cook</h3><p>372 vacancies<br>available</p>
</div>
<div class="cat" style="left:806px;top:1343px">
  <div class="icon"><svg width="40" height="40" viewBox="0 0 40 40" fill="none" stroke="#fff" stroke-width="2.5"><rect x="14" y="6" width="20" height="15" rx="2"/><circle cx="11" cy="20" r="3.5"/><path d="M5 34c0-6 3-9 6-9l8-4M18 12h12M18 16h8"/></svg></div>
  <h3>Education and teachers</h3><p>372 vacancies<br>available</p>
</div>

<h2 class="section-title" style="top:1743px">How it works</h2>
<p class="section-sub" style="top:1793px">We explain how you can find suitable<br>candidates for your open jobs</p>

<svg class="abs" style="left:0;top:1900px" width="1200" height="240" viewBox="0 0 1200 240" fill="none" stroke="#c8202f" stroke-width="3" stroke-dasharray="12 10">
  <path d="M280 160 C330 215 440 225 530 175"/>
  <path d="M690 90 C760 40 840 40 890 75"/>
</svg>
<svg class="abs" style="left:0;top:1900px" width="1200" height="240" viewBox="0 0 1200 240" fill="#c8202f">
  <path d="M538 170 l-14 -2 6 12z"/><path d="M896 80 l-4 -16 -10 10z"/>
</svg>

<div class="step-circle" style="left:125px;top:1920px"><svg width="70" height="76" viewBox="0 0 70 76" fill="none" stroke="#fff" stroke-width="4"><rect x="8" y="8" width="54" height="64" rx="5" fill="#fff" stroke="none"/><rect x="24" y="3" width="22" height="10" rx="2" fill="#fff" stroke="none"/><g stroke="#c8202f"><path d="M16 28l4 4 6-7M32 30h20M16 44l4 4 6-7M32 46h20M16 60l4 4 6-7M32 62h20"/></g></svg></div>
<div class="step-circle" style="left:516px;top:1920px"><svg width="86" height="60" viewBox="0 0 86 60" fill="#fff"><circle cx="43" cy="14" r="10"/><circle cx="18" cy="20" r="8"/><circle cx="68" cy="20" r="8"/><path d="M25 56c0-16 36-16 36 0z"/><path d="M2 54c0-14 26-14 28-6v6z"/><path d="M84 54c0-14-26-14-28-6v6z"/></svg></div>
<div class="step-circle" style="left:916px;top:1920px"><svg width="80" height="70" viewBox="0 0 80 70" fill="#fff"><rect x="4" y="4" width="32" height="22" rx="3"/><rect x="10" y="10" width="14" height="3" fill="#c8202f"/><rect x="10" y="16" width="20" height="3" fill="#c8202f"/><circle cx="56" cy="14" r="9"/><path d="M40 42c0-14 32-14 32 0z"/><circle cx="20" cy="38" r="8"/><path d="M4 66c0-16 32-16 32 0z"/><rect x="40" y="46" width="38" height="20" rx="2"/></svg></div>

<p class="step-text" style="left:79px;top:2153px;width:240px">Describe what kind of<br>candidate you want<br>for your job</p>
<p class="step-text" style="left:500px;top:2153px;width:200px">Select the<br>candidate who is<br>suitable for your<br>job</p>
<p class="step-text" style="left:870px;top:2153px;width:260px">Interview several<br>candidates for suitable<br>positions for the job</p>

<section class="about">
  <div class="about-photo" role="img" aria-label="Photo of three women meeting around a white table in a bright office"></div>
  <h2>About us</h2>
  <p>We provide employment opportunities for all of<br>you and also provide a place for recruiters to<br>look for suitable candidates for their<br>companies</p>
  <div class="stat" style="left:552px;width:178px"><b>20K</b><span>New job<br>opportunities</span></div>
  <div class="stat" style="left:747px;width:174px"><b>50+</b><span style="margin-top:21px">Company</span></div>
  <div class="stat" style="left:940px;width:175px"><b>50+</b><span>Helping<br>recruiters</span></div>
</section>

<section class="popular">
  <h2 class="section-title" style="top:65px;color:#fff">The most popular jobs for now</h2>
  <p class="section-sub" style="top:124px;color:#fff">We share job vacancies with those of you who<br>are looking for work, I hope this can help you all</p>
  <article class="job" style="left:83px">
    <div class="company"><i></i>Northbay</div>
    <div class="salary">$550/<small>Years</small></div>
    <h4>Developer Enginer</h4>
    <div class="type">Fulltime</div>
    <p class="desc">We are looking for candidates with<br>experience in the same field for 1 year</p>
    <div class="apply">Apply Job</div>
  </article>
  <article class="job" style="left:632px">
    <div class="company"><i style="background:#2a6ad8"></i>Kindred Social</div>
    <div class="salary">$250/<small>Years</small></div>
    <h4>Sosial media specialist</h4>
    <div class="type">Fulltime</div>
    <p class="desc">We are looking for candidates with<br>experience in the same field for 1 year</p>
    <div class="apply">Apply Job</div>
  </article>
</section>

<h2 class="section-title" style="top:3484px">success stories of several people who got jobs on our website</h2>
<p class="section-sub" style="top:3537px">Come see the stories and experiences of<br>everyone who has used our website</p>

<article class="story" style="left:90px"><div class="avatar" role="img" aria-label="Portrait photo of Michele"></div><h4>Michele</h4><p>It is very profitable to<br>be able to use this<br>website well</p></article>
<article class="story" style="left:440px"><div class="avatar" role="img" aria-label="Portrait photo of Andress"></div><h4>Andress</h4><p>I am very happy to be<br>able to help find a<br>decent job</p></article>
<article class="story" style="left:790px"><div class="avatar" role="img" aria-label="Portrait photo of Davide"></div><h4>Davide</h4><p style="left:24px;width:270px">It really helped me find<br>suitable candidates for<br>positions in my company</p></article>

<svg class="abs" style="left:94px;top:4002px" width="20" height="20" viewBox="0 0 20 20" fill="none" stroke="#333" stroke-width="2.5"><path d="M13 3l-7 7 7 7"/></svg>
<svg class="abs" style="left:1084px;top:4002px" width="20" height="20" viewBox="0 0 20 20" fill="none" stroke="#aaa" stroke-width="2.5"><path d="M7 3l7 7-7 7"/></svg>
<span class="dot" style="left:547px"></span>
<span class="dot idle" style="left:588px"></span>
<span class="dot idle" style="left:628px"></span>

<footer class="site-footer"></footer>
<div class="brand" style="left:87px;top:4160px">
  <span class="brand-mark" style="background:#fff"></span><span class="brand-name" style="color:#fff">kestrelwork</span>
</div>
<div class="brand-tag abs" style="left:121px;top:4188px;color:#f3c9cd">Careers made simple</div>
<span class="social" style="left:85px" aria-label="Social link"></span>
<span class="social" style="left:149px" aria-label="Social link"></span>
<span class="social" style="left:214px" aria-label="Social link"></span>
<div class="foot-col" style="left:617px;color:#fff"><h5>Service</h5><a href="#">Find Job</a><a href="#">Hire Telent</a><a href="#">Discovery Insight</a><a href="#">Consulting Solution</a></div>
<div class="foot-col" style="left:903px;color:#fff"><h5>Company</h5><a href="#">Thecnology</a><a href="#">Contact us</a><a href="#">About us</a><a href="#">Leadership</a></div>
<div class="foot-rule"></div>
<div class="foot-legal">All Right Reserved / Privacy Policy / Termn and use</div>

</body>
</html>
```